Verdana Crest New Website - Online Learning and Education

New Wordpress website for an online learning site that has courses, worksheets, quizzes, etc.
Updates

We would like something similar to this website: https://hallowaybridgeinstitute.example/mediation-skills-course/. But continue with the content of our current website: http://verdanacrestlearninghub.example

We would like something similar to this site: https://hallowaybridgeinstitute.example/mediation-skills-course/

Coding

Coded - Design and coding required

```html
<!DOCTYPE html>
<html lang="en">
<head>
<meta charset="utf-8">
<title>Verdana Crest – Online Learning</title>
<link rel="stylesheet" href="https://fonts.googleapis.com/css2?family=Montserrat:wght@400;600;700&family=Open+Sans:wght@400;600&display=swap">
<style>
:root{
  --navy:#1c3f6e;
  --navy-dark:#16335a;
  --red:#c8202f;
  --ink:#333a44;
  --muted:#6b7380;
  --line:#e1e4e8;
  --paper:#ffffff;
  --soft:#f1f2f4;
}
*{box-sizing:border-box;margin:0;padding:0}
html,body{width:1200px;height:2680px;overflow:hidden;background:var(--paper)}
body{font-family:"Open Sans",Arial,sans-serif;color:var(--ink);position:relative}
h1,h2,h3,.brand,.nav a,.btn{font-family:"Montserrat",Arial,sans-serif}

/* header */
.site-header{position:absolute;top:0;left:0;width:1200px;height:90px;background:var(--paper)}
.brand{position:absolute;left:120px;top:22px;display:flex;align-items:center;gap:14px;font-size:30px;font-weight:700;color:var(--navy);letter-spacing:1px}
.brand .dot{width:34px;height:34px;border-radius:50%;background:var(--red)}
.nav{position:absolute;right:0;top:0;height:70px;width:700px;background:var(--red);display:flex;align-items:center;justify-content:space-around;padding:0 40px 0 30px}
.nav a{color:#fff;text-decoration:none;font-size:15px;font-weight:600;letter-spacing:.5px}

/* hero */
.hero{position:absolute;top:90px;left:0;width:1200px;height:800px;background:linear-gradient(120deg,#4a3a2c 0%,#8a6a4a 35%,#c9b79a 60%,#6f5a44 100%)}
.hero-card{position:absolute;left:0;top:300px;width:420px;height:400px;background:rgba(28,63,110,.82);padding:60px 40px 0 56px;color:#fff}
.hero-card h1{font-size:52px;font-weight:700;letter-spacing:2px;line-height:1.15;margin-bottom:24px}
.hero-card p{font-size:16px;line-height:1.55;opacity:.92;margin-bottom:34px}
.btn{display:inline-block;background:var(--red);color:#fff;font-size:15px;font-weight:600;padding:14px 28px;text-decoration:none}

/* main column */
.main{position:absolute;top:950px;left:120px;width:690px}
h2.section-title{font-size:36px;font-weight:700;color:var(--navy);letter-spacing:1px}
.rule{width:70px;height:4px;background:var(--red);margin:18px 0 26px}
.main p{font-size:15px;line-height:1.7;color:var(--muted);margin-bottom:18px}
.quote{margin:50px 0 50px;background:var(--soft);border-left:5px solid var(--navy);padding:34px 40px;font-size:15px;line-height:1.65;color:var(--muted);font-style:italic}
.quote cite{display:block;text-align:right;margin-top:14px;font-size:14px}

/* sidebar */
.sidebar{position:absolute;top:930px;left:840px;width:240px;display:flex;flex-direction:column}
.sample-box{background:var(--navy);color:#fff;text-align:center;padding:22px 20px;font-family:"Montserrat",sans-serif;font-size:20px;font-weight:600;line-height:1.35;border-bottom:4px solid var(--red)}
.lesson-list{list-style:none;padding:18px 0 22px 10px}
.lesson-list li{display:flex;align-items:center;gap:12px;font-size:14px;color:var(--ink);height:36px;white-space:nowrap}
.course-box{background:var(--red);color:#fff;text-align:center;padding:22px 20px;font-family:"Montserrat",sans-serif;font-size:22px;font-weight:600;line-height:1.3}
.course-list{list-style:none}
.course-list li{display:flex;justify-content:space-between;align-items:center;height:44px;border-bottom:1px solid var(--line);padding:0 8px;font-size:14px}

/* samples */
.samples{position:absolute;top:1800px;left:0;width:1200px;height:560px;background:var(--soft);text-align:center}
.samples h2{margin-top:36px}
.samples .rule{margin:16px auto 36px}
.screens{display:flex;justify-content:center;gap:60px}
.screen{width:440px;height:370px;background:#fff;border:1px solid #cfd3d9;padding:12px}
.screen .bar{height:16px;background:#dfe2e6;margin-bottom:10px}
.screen .fill{height:318px;background:linear-gradient(180deg,#e9ecef,#cdd3da)}
.screen.two .fill{background:linear-gradient(180deg,#eef0f2 0%,#e2e6ea 50%,#7fc9b8 51%,#e6e9ec 70%)}

/* footer */
.site-footer{position:absolute;top:2360px;left:0;width:1200px;height:320px;background:var(--navy);color:#fff}
.footer-brand{position:absolute;top:44px;left:0;width:1200px;display:flex;justify-content:center;align-items:center;gap:16px;font-family:"Montserrat",sans-serif;font-size:44px;font-weight:700;letter-spacing:2px}
.footer-brand .dot{width:46px;height:46px;border-radius:50%;background:var(--red)}
.contacts{position:absolute;top:170px;left:120px;width:960px;display:flex;justify-content:space-between}
.contact{display:flex;gap:14px;align-items:flex-start;width:280px}
.contact h3{font-size:17px;font-weight:600;margin-bottom:6px}
.contact p{font-size:14px;opacity:.85}
.copyright{position:absolute;bottom:0;left:0;width:1200px;height:48px;background:var(--navy-dark);text-align:center;line-height:48px;font-size:13px;opacity:.95}
</style>
</head>
<body>

<header class="site-header">
  <div class="brand"><span class="dot"></span>Verdana Crest</div>
  <nav class="nav">
    <a>HOME</a><a>ABOUT US</a><a>COURSES</a><a>WORKSHEETS</a><a>QUIZZES</a><a>CONTACT US</a>
  </nav>
</header>

<section class="hero" role="img" aria-label="Photo of a student with headphones reading a book in a library">
  <div class="hero-card">
    <h1>Verdana Crest</h1>
    <p>Learn at your own pace with clear lessons, practical worksheets and short quizzes that help you build lasting habits for work and life.</p>
    <a class="btn">Read More</a>
  </div>
</section>

<div class="main">
  <section class="welcome">
    <h2 class="section-title">WELCOME TO VERDANA CREST!</h2>
    <div class="rule"></div>
    <p>Verdana Crest is an online learning system that offers short, focused courses for people who want to grow. Our lessons are built by experienced trainers and designed to fit into busy days, with clear steps and simple exercises you can use right away at home, at school or in the workplace.</p>
    <p>Each course comes with worksheets and quizzes so you can test what you learn and track your progress. Study on any device and come back whenever you are ready.</p>
    <a class="btn">READ MORE</a>
  </section>

  <blockquote class="quote">
    These courses changed the way I plan my week. The lessons are short and clear, the worksheets are easy to follow, and the quizzes helped me see how much I had learned. I now recommend the program to everyone on my team and look forward to each new course.
    <cite>Anna Reyes / 14 May 2019</cite>
  </blockquote>

  <section class="styles">
    <h2 class="section-title">DIFFERENT LEARNING STYLES</h2>
    <div class="rule"></div>
    <p>People learn in different ways, so every course mixes formats. Read short texts, listen to audio lessons, watch clear videos and practise with worksheets and quizzes. Choose the style that suits you best and switch whenever you like as you move through each module.</p>
  </section>
</div>

<aside class="sidebar">
  <div class="sample-box">Sample Our online learning Course</div>
  <ul class="lesson-list">
    <li><svg width="14" height="14" viewBox="0 0 14 14"><path d="M2 7l3 3 7-7" fill="none" stroke="#1c3f6e" stroke-width="2"/></svg>Become a Better Listener</li>
    <li><svg width="14" height="14" viewBox="0 0 14 14"><path d="M2 7l3 3 7-7" fill="none" stroke="#1c3f6e" stroke-width="2"/></svg>Proactive Decision Making</li>
    <li><svg width="14" height="14" viewBox="0 0 14 14"><path d="M2 7l3 3 7-7" fill="none" stroke="#1c3f6e" stroke-width="2"/></svg>Improving Self Awareness</li>
    <li><svg width="14" height="14" viewBox="0 0 14 14"><path d="M2 7l3 3 7-7" fill="none" stroke="#1c3f6e" stroke-width="2"/></svg>The Power of Priorities</li>
    <li><svg width="14" height="14" viewBox="0 0 14 14"><path d="M2 7l3 3 7-7" fill="none" stroke="#1c3f6e" stroke-width="2"/></svg>Mastering Habits</li>
    <li><svg width="14" height="14" viewBox="0 0 14 14"><path d="M2 7l3 3 7-7" fill="none" stroke="#1c3f6e" stroke-width="2"/></svg>Managing a To-Do List</li>
    <li><svg width="14" height="14" viewBox="0 0 14 14"><path d="M2 7l3 3 7-7" fill="none" stroke="#1c3f6e" stroke-width="2"/></svg>Perfection: The Enemy of Progress</li>
  </ul>

  <div class="course-box">Take The Full Course Now</div>
  <ul class="course-list">
    <li>Start your first lesson<svg width="16" height="16" viewBox="0 0 16 16"><circle cx="8" cy="8" r="8" fill="#333a44"/><path d="M6 4l4 4-4 4" fill="none" stroke="#fff" stroke-width="2"/></svg></li>
    <li>Download worksheets<svg width="16" height="16" viewBox="0 0 16 16"><circle cx="8" cy="8" r="8" fill="#333a44"/><path d="M6 4l4 4-4 4" fill="none" stroke="#fff" stroke-width="2"/></svg></li>
    <li>Take a short quiz<svg width="16" height="16" viewBox="0 0 16 16"><circle cx="8" cy="8" r="8" fill="#333a44"/><path d="M6 4l4 4-4 4" fill="none" stroke="#fff" stroke-width="2"/></svg></li>
    <li>Track your progress<svg width="16" height="16" viewBox="0 0 16 16"><circle cx="8" cy="8" r="8" fill="#333a44"/><path d="M6 4l4 4-4 4" fill="none" stroke="#fff" stroke-width="2"/></svg></li>
    <li>Join a live session<svg width="16" height="16" viewBox="0 0 16 16"><circle cx="8" cy="8" r="8" fill="#333a44"/><path d="M6 4l4 4-4 4" fill="none" stroke="#fff" stroke-width="2"/></svg></li>
    <li>Review your notes<svg width="16" height="16" viewBox="0 0 16 16"><circle cx="8" cy="8" r="8" fill="#333a44"/><path d="M6 4l4 4-4 4" fill="none" stroke="#fff" stroke-width="2"/></svg></li>
    <li>Earn your certificate<svg width="16" height="16" viewBox="0 0 16 16"><circle cx="8" cy="8" r="8" fill="#333a44"/><path d="M6 4l4 4-4 4" fill="none" stroke="#fff" stroke-width="2"/></svg></li>
  </ul>
</aside>

<section class="samples">
  <h2 class="section-title">SAMPLE SCREENS</h2>
  <div class="rule"></div>
  <div class="screens">
    <div class="screen"><div class="bar"></div><div class="fill" role="img" aria-label="Screenshot of a course lesson page"></div></div>
    <div class="screen two"><div class="bar"></div><div class="fill" role="img" aria-label="Screenshot of a course dashboard page"></div></div>
  </div>
</section>

<footer class="site-footer">
  <div class="footer-brand"><span class="dot"></span>Verdana Crest</div>
  <div class="contacts">
    <div class="contact">
      <svg width="30" height="30" viewBox="0 0 30 30"><circle cx="15" cy="15" r="15" fill="#fff"/><path d="M15 7a5 5 0 0 0-5 5c0 4 5 10 5 10s5-6 5-10a5 5 0 0 0-5-5z" fill="#1c3f6e"/><circle cx="15" cy="12" r="2" fill="#fff"/></svg>
      <div><h3>Address :</h3><p>1200 Lorne Street, Harbor Town</p></div>
    </div>
    <div class="contact">
      <svg width="30" height="30" viewBox="0 0 30 30"><circle cx="15" cy="15" r="15" fill="#fff"/><rect x="8" y="10" width="14" height="10" fill="none" stroke="#1c3f6e" stroke-width="2"/><path d="M8 10l7 6 7-6" fill="none" stroke="#1c3f6e" stroke-width="2"/></svg>
      <div><h3>Email</h3><p>info@verdanacrest.example</p></div>
    </div>
    <div class="contact">
      <svg width="30" height="30" viewBox="0 0 30 30"><circle cx="15" cy="15" r="15" fill="#fff"/><path d="M10 8h3l2 4-2 2a10 10 0 0 0 3 3l2-2 4 2v3a2 2 0 0 1-2 2A12 12 0 0 1 8 10a2 2 0 0 1 2-2z" fill="#1c3f6e"/></svg>
      <div><h3>Phone</h3><p>Mobile : 555-014-2280</p></div>
    </div>
  </div>
  <div class="copyright">© Copyright 2019 Verdana Crest. All rights reserved.</div>
</footer>

</body>
</html>
```